KLVB Canberra Pty Ltd

Want something creative and that catches your eye. We are a traffic control companythat offers all aspects of traffic control from planning to roadworks.

Contact Information for Business Card

Derek Oswin - Director
Ph: 0418 372 506
Email: derek@klvb-example.com.au
27 Wattle Grove ct Banfield ACT 2911

```html
<!DOCTYPE html>
<html lang="en">
<head>
<meta charset="utf-8">
<title>KLVB – Business Card</title>
<link href="https://fonts.googleapis.com/css2?family=Michroma&display=swap" rel="stylesheet">
<style>
  :root {
    --bg-center: #5a5a5a;
    --bg-edge: #1e1e1e;
    --card: #2b2b2b;
    --card-panel: #222222;
    --stripe-light: #d4b62a;
    --stripe-dark: #8f7d12;
    --text-light: #e4e4e4;
    --text-muted: #bdbdbd;
    --gold: #b39a2c;
    --brand-dot: #8cc63f;
  }
  * { margin: 0; padding: 0; box-sizing: border-box; }
  html, body { width: 1200px; height: 900px; overflow: hidden; }
  body {
    position: relative;
    background: radial-gradient(ellipse at 50% 35%, var(--bg-center) 0%, var(--bg-edge) 75%);
    font-family: "Michroma", sans-serif;
  }
  .card {
    position: absolute;
    width: 600px;
    height: 343px;
    background: var(--card);
    box-shadow: 0 14px 30px rgba(0,0,0,0.55);
    overflow: hidden;
  }
  .card--front { left: 60px; top: 80px; }
  .card--back { left: 540px; top: 477px; }
  .card__hazard { position: absolute; inset: 0; width: 600px; height: 343px; }
  .brand {
    position: absolute;
    left: 120px;
    top: 150px;
    display: flex;
    align-items: center;
    gap: 16px;
  }
  .brand__dot {
    width: 44px; height: 44px;
    border-radius: 50%;
    background: var(--brand-dot);
  }
  .brand__name {
    font-size: 22px;
    color: var(--text-muted);
    letter-spacing: 1px;
    white-space: nowrap;
  }
  .contact-name {
    position: absolute;
    left: 40px; top: 118px;
    font-size: 26px;
    font-weight: 400;
    color: var(--text-light);
    letter-spacing: 1px;
    white-space: nowrap;
  }
  .contact-role {
    position: absolute;
    left: 96px; top: 160px;
    font-size: 22px;
    color: var(--gold);
    letter-spacing: 2px;
  }
  .contact-details {
    position: absolute;
    left: 40px; bottom: 34px;
    list-style: none;
    font-size: 12px;
    line-height: 1.45;
    color: var(--text-muted);
    text-transform: uppercase;
    letter-spacing: 1px;
    white-space: nowrap;
  }
</style>
</head>
<body>
  <svg width="0" height="0" style="position:absolute">
    <defs>
      <linearGradient id="stripe-gold" x1="0" y1="0" x2="1" y2="1">
        <stop offset="0" stop-color="var(--stripe-light)"/>
        <stop offset="1" stop-color="var(--stripe-dark)"/>
      </linearGradient>
      <g id="hazard-stripes">
        <polygon points="300,0 600,0 600,343 600,343 330,200" fill="var(--card-panel)"/>
        <polygon points="440,-10 570,-10 590,22 460,22" fill="url(#stripe-gold)"/>
        <polygon points="452,40 582,40 602,78 472,78" fill="url(#stripe-gold)"/>
        <polygon points="464,96 594,96 614,134 484,134" fill="url(#stripe-gold)"/>
        <polygon points="476,152 606,152 626,190 496,190" fill="url(#stripe-gold)"/>
        <polygon points="488,208 618,208 638,246 508,246" fill="url(#stripe-gold)"/>
        <polygon points="500,264 630,264 650,302 520,302" fill="url(#stripe-gold)"/>
        <polygon points="512,320 642,320 662,358 532,358" fill="url(#stripe-gold)"/>
      </g>
    </defs>
  </svg>

  <section class="card card--front">
    <svg class="card__hazard" viewBox="0 0 600 343"><use href="#hazard-stripes"/></svg>
    <div class="brand">
      <span class="brand__dot"></span>
      <span class="brand__name">KLVB Pty Ltd</span>
    </div>
  </section>

  <section class="card card--back">
    <svg class="card__hazard" viewBox="0 0 600 343"><use href="#hazard-stripes"/></svg>
    <h1 class="contact-name">DEREK OSWIN</h1>
    <p class="contact-role">DIRECTOR</p>
    <ul class="contact-details">
      <li>Ph: 0418 372 506</li>
      <li>Email: derek@klvb-example.com.au</li>
      <li>27 Wattle Grove ct Banfield ACT 2911</li>
    </ul>
  </section>
</body>
</html>
```